Trovanta Overview and Demo Presentation

Objective:
Create a bold, visually engaging PowerPoint deck to present Trovanta’s sales process and system demo to local movers, emphasizing ease of use, increased profitability, and operational efficiency.
Key Elements:
• Design: High-impact graphics with Trovanta branding, minimal text, and clean layouts.
• Content: Step-by-step sales process, key selling points, system demo walkthrough, and a compelling call-to-action.
• Live Demo: Showcase Trovanta’s platform, focusing on instant guaranteed pricing, streamlined booking, and support features.
Deliverables:
A dynamic presentation designed to educate and convert local movers into Trovanta partners, ensuring seamless flow and strong audience engagement.

Target Market(s)

Local Movers

Industry/Entity Type

Household Goods Moving

Font styles to use
Sans Serif

Colors
0054AA
0677BA
7BADD7
CADEEF
E8F1F8
FFC000
F8CF3A
FAE287
FDF2CF
FEFAEE

Requirements
Must have
• Project Brief: Trovanta Sales Process Presentation Objective: Create a bold, visually engaging PowerPoint deck to present Trovanta’s sales process and system demo to local movers, emphasizing ease of use, increased profitability, and operational efficiency. Key Elements: • Design: High-impact graphics with Trovanta branding, minimal text, and clean layouts. • Content: Step-by-step sales process, key selling points, system demo walkthrough, and a compelling call-to-action. • Live Demo: Showcase Trovanta’s platform, focusing on instant guaranteed pricing, streamlined booking, and support features. Deliverables: A dynamic presentation designed to educate and convert local movers into Trovanta partners, ensuring seamless flow and strong audience engagement.

```html
<!DOCTYPE html>
<html lang="en">
<head>
<meta charset="utf-8">
<title>Trovanta Overview Deck</title>
<link href="https://fonts.googleapis.com/css2?family=Poppins:wght@500;600;700&family=Roboto:wght@400;500;700&display=swap" rel="stylesheet">
<style>
:root{
  --blue:#2b57e0;
  --blue-deep:#1f47c9;
  --yellow:#ffc94d;
  --ink:#1d1d1f;
  --grey:#555a63;
  --bg:#e1e1e1;
  --card:#ffffff;
  --photo-a:#c9b18a;
  --photo-b:#8a94a8;
}
*{margin:0;padding:0;box-sizing:border-box}
html,body{width:1031px;height:1200px;overflow:hidden;background:var(--bg)}
body{font-family:Roboto,Arial,sans-serif;color:var(--ink)}
.board{position:absolute;left:0;top:0;width:1781px;height:2072px;transform:scale(.5789);transform-origin:0 0}
.slide{position:absolute;width:765px;height:430px;background:#fff;overflow:hidden;box-shadow:0 2px 6px rgba(0,0,0,.12)}
.abs{position:absolute}
.header{position:absolute;left:0;top:0}
.slide-title{position:absolute;left:35px;top:8px;font:700 24px Poppins,sans-serif;color:#fff;white-space:nowrap}
.slide-title em{font-style:normal;color:var(--yellow)}
.footer{position:absolute;left:0;bottom:0;width:765px;height:18px;background:var(--blue);color:#fff;font-size:7.5px;display:flex;align-items:center;justify-content:space-between;padding:0 34px}
.footer b{font-weight:700}
.footer b span{color:var(--yellow)}
.photo{position:absolute;background:linear-gradient(135deg,var(--photo-a),var(--photo-b))}
.center{text-align:center}
/* cover */
.cover{background:var(--blue)}
.brand{position:absolute;left:34px;top:20px;font:600 19px Poppins,sans-serif;color:#fff}
.eyebrow{position:absolute;left:34px;top:116px;font:600 10px Poppins,sans-serif;color:var(--yellow)}
.cover h1{position:absolute;left:34px;top:140px;font:700 26.5px/40px Poppins,sans-serif;color:#fff}
.btn{position:absolute;left:34px;top:238px;width:107px;height:31px;border-radius:16px;background:var(--yellow);color:var(--blue-deep);font:600 11px Poppins,sans-serif;display:flex;align-items:center;justify-content:center}
.social{position:absolute;top:292px;width:22px;height:22px;border-radius:50%;background:var(--yellow)}
/* leadership */
.lead-card{position:absolute;background:var(--card);border-radius:6px;box-shadow:0 2px 8px rgba(0,0,0,.1);text-align:center}
.avatar{position:absolute;width:62px;height:62px;border-radius:50%;border:3px solid #fff;background:linear-gradient(160deg,#8b93a4,#3a4252);box-shadow:0 1px 4px rgba(0,0,0,.2)}
.lead-name{font:700 11px Roboto,sans-serif}
.lead-role{font-size:7px;color:var(--grey);margin-top:5px}
/* about */
.about-text{position:absolute;left:65px;top:60px;width:635px;font-size:10.5px;line-height:19.5px;color:var(--grey);text-align:center}
.about-text p+p{margin-top:7px}
/* steps */
.step-num{position:absolute;width:56px;height:56px;border-radius:50%;background:var(--blue);border:3px solid #fff;box-shadow:0 0 0 2px #d9e0f5;color:var(--yellow);font:700 24px Poppins,sans-serif;display:flex;align-items:center;justify-content:center}
.step{position:absolute;width:190px;font-size:8px;line-height:12.5px;color:var(--grey)}
.step h4{font:500 9.5px Roboto,sans-serif;color:var(--ink);margin-bottom:6px}
.step.left{text-align:right}
/* vision */
.vision-col{position:absolute;top:268px;width:217px;text-align:center}
.vision-col h3{font:500 13px Roboto,sans-serif;margin-bottom:8px}
.vision-col .lead{font:500 9px/14px Roboto,sans-serif;color:#333}
.vision-col .lead span{color:var(--blue)}
.vision-col .body{font-size:7.6px;line-height:12.5px;color:var(--grey);margin-top:8px}
/* stats */
.stat-card{position:absolute;width:161px;height:190px;background:#fff;border-radius:6px;box-shadow:0 2px 10px rgba(0,0,0,.1);text-align:center}
.stat-num{font:700 23px Poppins,sans-serif;color:var(--yellow)}
.stat-rule{width:30px;height:2px;background:var(--blue);margin:6px auto 10px}
.stat-label{font-size:8.5px;color:#333}
.stat-band{height:28px;background:var(--blue);color:var(--yellow);font:500 11px Roboto,sans-serif;display:flex;align-items:center;justify-content:center;margin:15px 0 10px}
/* problems */
.problem{position:absolute;left:34px;width:330px;height:76px;background:#fff;box-shadow:0 2px 8px rgba(0,0,0,.1)}
.problem .strip{position:absolute;left:0;top:0;width:22px;height:76px;background:var(--blue)}
.problem .icon{position:absolute;left:18px;top:10px;width:56px;height:56px;border-radius:50%;background:var(--yellow);border:3px solid #fff}
.problem .icon svg{position:absolute;left:13px;top:13px}
.problem h4{position:absolute;left:87px;top:10px;font:500 11px Roboto,sans-serif}
.problem p{position:absolute;left:87px;top:30px;width:230px;font-size:8px;line-height:16px;color:var(--grey)}
/* solution */
.sol-head{position:absolute;left:33px;top:80px;font:500 15.5px Roboto,sans-serif}
.sol-list{position:absolute;left:33px;top:112px;width:300px}
.sol-item h4{font:500 10px Roboto,sans-serif;display:flex;align-items:center;gap:6px}
.sol-item h4 i{width:9px;height:9px;border-radius:50%;background:var(--blue);display:inline-block;position:relative}
.sol-item h4 i::after{content:"";position:absolute;left:2.5px;top:1.5px;width:2.5px;height:4px;border:solid #fff;border-width:0 1.2px 1.2px 0;transform:rotate(45deg)}
.sol-item p{font-size:8.5px;line-height:17px;color:var(--grey);margin-top:6px;margin-bottom:10px}
</style>
</head>
<body>
<div class="board">

  <!-- Cover -->
  <section class="slide cover" style="left:69px;top:75px">
    <svg class="abs" width="765" height="430" style="left:0;top:0">
      <polygon points="425,0 765,0 765,430 462,430 338,290" fill="#2550d4" opacity=".55" transform="translate(-38,0)"/>
    </svg>
    <div class="photo" role="img" aria-label="Movers carrying cardboard boxes from a truck while a young couple watches outside a house" style="left:0;top:0;width:765px;height:430px;clip-path:polygon(425px 0,765px 0,765px 430px,462px 430px,338px 290px);background:linear-gradient(135deg,#b9c3cf,#d2a86a 60%,#7f8a9c)"></div>
    <div class="brand">Trovanta</div>
    <div class="eyebrow">WELCOME TO TROVANTA</div>
    <h1>MOVING FOR THE<br>NEXT GENERATION</h1>
    <div class="btn">CONTACT US</div>
    <span class="social" style="left:37px"></span>
    <span class="social" style="left:65px"></span>
    <span class="social" style="left:93px"></span>
    <span class="social" style="left:121px"></span>
  </section>

  <!-- Leadership -->
  <section class="slide" style="left:926px;top:75px">
    <svg class="header" width="765" height="60"><polygon points="0,0 648,0 625,46 0,46" fill="var(--blue)"/><polygon points="648,0 765,0 765,46 625,46" fill="var(--yellow)"/><polygon points="0,46 408,46 402,58 0,58" fill="var(--yellow)"/></svg>
    <div class="slide-title"><em>Leadership</em> Team</div>
    <svg class="abs" width="765" height="430" style="left:0;top:0">
      <g stroke="var(--blue)" stroke-width="1.5" stroke-dasharray="2 3" fill="none">
        <path d="M123,158 H318 M449,158 H640 M123,158 V250 M295,158 V250 M467,158 V250 M640,158 V250"/>
      </g>
      <g fill="var(--yellow)"><circle cx="123" cy="158" r="3"/><circle cx="295" cy="158" r="3"/><circle cx="467" cy="158" r="3"/><circle cx="640" cy="158" r="3"/></g>
    </svg>
    <div class="lead-card" style="left:318px;top:112px;width:131px;height:84px;padding-top:44px"><div class="lead-name">Dale Forsythe</div><div class="lead-role">Chief Executive Officer</div></div>
    <div class="avatar" role="img" aria-label="Portrait photo of the chief executive officer" style="left:351px;top:82px"></div>
    <div class="lead-card" style="left:45px;top:278px;width:160px;height:86px;padding-top:45px"><div class="lead-name">Owen Marsh</div><div class="lead-role">Chief Operations Officer</div></div>
    <div class="lead-card" style="left:217px;top:278px;width:160px;height:86px;padding-top:45px"><div class="lead-name">Cole Prentiss</div><div class="lead-role">Founder CIO</div></div>
    <div class="lead-card" style="left:389px;top:278px;width:160px;height:86px;padding-top:45px"><div class="lead-name">Luis Varga</div><div class="lead-role">SVP B2C</div></div>
    <div class="lead-card" style="left:561px;top:278px;width:160px;height:86px;padding-top:45px"><div class="lead-name">Helen Dorsey</div><div class="lead-role">VP B2C</div></div>
    <div class="avatar" role="img" aria-label="Portrait photo of the chief operations officer" style="left:94px;top:247px"></div>
    <div class="avatar" role="img" aria-label="Portrait photo of the founder and CIO" style="left:266px;top:247px"></div>
    <div class="avatar" role="img" aria-label="Portrait photo of the SVP B2C" style="left:438px;top:247px"></div>
    <div class="avatar" role="img" aria-label="Portrait photo of the VP B2C" style="left:610px;top:247px"></div>
    <div class="footer"><b>PAGE | <span>05</span></b><span>© 2024 Trovanta | All Rights Reserved</span><span>www.trovanta.com</span></div>
  </section>

  <!-- About -->
  <section class="slide" style="left:69px;top:567px">
    <svg class="header" width="765" height="60"><polygon points="0,0 648,0 625,46 0,46" fill="var(--blue)"/><polygon points="648,0 765,0 765,46 625,46" fill="var(--yellow)"/><polygon points="0,46 408,46 402,58 0,58" fill="var(--yellow)"/></svg>
    <div class="slide-title">About <em>Us</em></div>
    <div class="about-text">
      <p>Trovanta is the next logical evolution in professional moving. Professional moving clients have battled soaring prices, acute capacity problems and deteriorating service levels.</p>
      <p>Trovanta was founded by lifelong moving professionals who have developed the answer to better moving services. Poised as THE industry disruptor, we deliver faster, offer guaranteed prices and even offer no credit check financing options. We are a technology first organization using proprietary software to deliver moving's best service experience.</p>
    </div>
    <div class="photo" role="img" aria-label="Two movers carrying a yellow sofa" style="left:15px;top:250px;width:220px;height:160px;background:linear-gradient(180deg,#f5f5f5,#f2d35a 55%,#2c3b5c)"></div>
    <div class="photo" role="img" aria-label="White moving truck" style="left:255px;top:278px;width:235px;height:106px;background:linear-gradient(180deg,#f3f4f8,#dfe3ec 70%,#3a3d44)"></div>
    <div class="photo" role="img" aria-label="Mover with clipboard beside stacked boxes" style="left:515px;top:215px;width:245px;height:197px;background:linear-gradient(135deg,#f7f7f7,#c49a6c 50%,#2a3553)"></div>
    <div class="footer"><b>PAGE | <span>02</span></b><span>© 2024 Trovanta | All Rights Reserved</span><span>www.trovanta.com</span></div>
  </section>

  <!-- How it works -->
  <section class="slide" style="left:926px;top:567px">
    <svg class="header" width="765" height="60"><polygon points="0,0 648,0 625,46 0,46" fill="var(--blue)"/><polygon points="648,0 765,0 765,46 625,46" fill="var(--yellow)"/><polygon points="0,46 408,46 402,58 0,58" fill="var(--yellow)"/></svg>
    <div class="slide-title">How It <em>Works</em></div>
    <div class="photo" role="img" aria-label="Smiling mover holding stacked cardboard boxes" style="left:297px;top:88px;width:170px;height:282px;border:3px solid var(--yellow);background:linear-gradient(180deg,#dfe3ea,#c8a06e 60%,#2f3d66)"></div>
    <div class="step-num" style="left:256px;top:80px">01</div>
    <div class="step-num" style="left:256px;top:200px">02</div>
    <div class="step-num" style="left:256px;top:320px">03</div>
    <div class="step-num" style="left:455px;top:80px">04</div>
    <div class="step-num" style="left:455px;top:195px">05</div>
    <div class="step-num" style="left:455px;top:320px">06</div>
    <div class="step left" style="left:47px;top:92px"><h4>SPOT AN OPPORTUNITY</h4>Do not let a long-distance move prospect slip away.</div>
    <div class="step left" style="left:47px;top:212px"><h4>GET A QUOTE</h4>Quickly input details on Trovanta.com.</div>
    <div class="step left" style="left:47px;top:332px"><h4>SET YOUR PRICE</h4>Offer a suitable price to your customer and secure a deal.</div>
    <div class="step" style="left:527px;top:92px"><h4>SEAMLESS SCHEDULING</h4>Use Trovanta.com to schedule the service. Just pay the deposit and leave the rest to us. You can even take advantage of our move concierge if that is easier.</div>
    <div class="step" style="left:527px;top:206px"><h4>FLEXIBLE PRICING STRUCTURE</h4>You decide the charges. We only bill you, letting you keep your desired profit.</div>
    <div class="step" style="left:527px;top:332px"><h4>STAY INFORMED</h4>We ensure constant communication so you can update your customers at every step.</div>
    <div class="footer"><b>PAGE | <span>06</span></b><span>© 2024 Trovanta | All Rights Reserved</span><span>www.trovanta.com</span></div>
  </section>

  <!-- Vision -->
  <section class="slide" style="left:69px;top:1060px">
    <svg class="header" width="765" height="60"><polygon points="0,0 648,0 625,46 0,46" fill="var(--blue)"/><polygon points="648,0 765,0 765,46 625,46" fill="var(--yellow)"/><polygon points="0,46 408,46 402,58 0,58" fill="var(--yellow)"/></svg>
    <div class="slide-title">Our <em>Vision</em></div>
    <div class="abs center" style="left:0;top:76px;width:765px;font:500 11.5px Roboto,sans-serif">The Traditional Moving Industry Is Broken, Outdated, Inefficient, And Unable To Change.</div>
    <div class="photo" role="img" aria-label="Movers loading furniture and boxes in a warehouse" style="left:37px;top:110px;width:217px;height:148px;background:linear-gradient(135deg,#e6e2dc,#c69a68 55%,#3a4670)"></div>
    <div class="photo" role="img" aria-label="Mover with clipboard talking to a customer holding a box" style="left:274px;top:110px;width:217px;height:148px;background:linear-gradient(135deg,#a98a66,#d08a3e 50%,#6d8b4a)"></div>
    <div class="photo" role="img" aria-label="Woman unpacking boxes in a bright living room" style="left:511px;top:110px;width:217px;height:148px;background:linear-gradient(135deg,#f1efec,#d9b58c 55%,#9aa3b0)"></div>
    <div class="vision-col" style="left:37px"><h3>OUR VISION</h3><div class="lead">Revolutionize The Moving Industry By Providing Great Value To Everyone Involved</div><div class="body">Trovanta Customers - Consumers, Movers, Corporate Clients, and Relocation Management Companies all receive better value with Trovanta than anywhere else.</div></div>
    <div class="vision-col" style="left:274px"><h3>OUR MISSION</h3><div class="lead">Disrupt a <span>$86b</span> Sleepy Giant Of an Inefficient Industry</div><div class="body">Trovanta's deep understanding of the professional moving industry, supported by extensive market research has set Trovanta up for ultimate success in disrupting this industry by creating cost-saving efficiencies throughout.</div></div>
    <div class="vision-col" style="left:511px"><h3>OUR GOAL</h3><div class="lead" style="margin-top:4px">Becoming The Moving Platform Of Choice</div><div class="body" style="margin-top:14px">As Trovanta's market share grows, the customer acquisition cost and operational cost plummets. This creates even more market penetration, more efficiencies, and exponential growth.</div></div>
    <div class="footer"><b>PAGE | <span>03</span></b><span>© 2024 Trovanta | All Rights Reserved</span><span>www.trovanta.com</span></div>
  </section>

  <!-- Revolutionizing -->
  <section class="slide" style="left:926px;top:1060px">
    <svg class="header" width="765" height="60"><polygon points="0,0 648,0 625,46 0,46" fill="var(--blue)"/><polygon points="648,0 765,0 765,46 625,46" fill="var(--yellow)"/><polygon points="0,46 408,46 402,58 0,58" fill="var(--yellow)"/></svg>
    <div class="slide-title">Revolutionizing</div>
    <div class="photo" role="img" aria-label="Two movers passing a box out of a moving truck" style="left:34px;top:86px;width:327px;height:289px;background:linear-gradient(135deg,#6b7080,#c99c62 50%,#d8dde3)"></div>
    <div class="abs" style="left:399px;top:82px;font:500 11.5px Roboto,sans-serif">The Moving Industry With Ai</div>
    <div class="abs" style="left:399px;top:108px;width:335px;font-size:10px;line-height:17.5px;color:var(--grey)">Trovanta is transforming the $90-100B moving industry by leveraging AI, GPS, and automated compliance to deliver the first instant guaranteed pricing platform. We're cutting out inefficiencies and middlemen to improve costs and service quality.</div>
    <div class="stat-card" style="left:399px;top:196px;padding-top:10px"><div class="stat-num">$1.9M</div><div class="stat-rule"></div><div class="stat-label">Revenue, Successfully, Raised</div><div class="stat-band">TO BUILD</div><div class="stat-num">$5</div><div class="stat-rule"></div><div class="stat-label">Appraised, Tech Stack</div></div>
    <div class="stat-card" style="left:568px;top:196px;padding-top:10px"><div class="stat-num">$500K</div><div class="stat-rule"></div><div class="stat-label">Additional, Raise</div><div class="stat-band">TO PROVE</div><div class="stat-num">B21</div><div class="stat-rule"></div><div class="stat-label">Successful, Model</div></div>
    <div class="footer"><b>PAGE | <span>07</span></b><span>© 2024 Trovanta | All Rights Reserved</span><span>www.trovanta.com</span></div>
  </section>

  <!-- Problems -->
  <section class="slide" style="left:69px;top:1552px">
    <svg class="header" width="765" height="60"><polygon points="0,0 648,0 625,46 0,46" fill="var(--blue)"/><polygon points="648,0 765,0 765,46 625,46" fill="var(--yellow)"/><polygon points="0,46 408,46 402,58 0,58" fill="var(--yellow)"/></svg>
    <div class="slide-title">Moving's <em>Problems</em></div>
    <div class="problem" style="top:75px"><span class="strip"></span><span class="icon"><svg width="24" height="24" viewBox="0 0 24 24"><circle cx="12" cy="10" r="7" fill="none" stroke="var(--blue)" stroke-width="2"/><text x="12" y="14" font-size="10" font-family="Roboto" font-weight="700" text-anchor="middle" fill="var(--blue)">$</text><path d="M2 21h20" stroke="var(--blue)" stroke-width="2"/></svg></span><h4>Cost</h4><p>Moving cost has skyrocketed over the last three years. Charges have increased 38% since 2018.</p></div>
    <div class="problem" style="top:157px"><span class="strip"></span><span class="icon"><svg width="24" height="24" viewBox="0 0 24 24"><rect x="1" y="6" width="13" height="10" fill="var(--blue)"/><path d="M14 9h5l4 4v3h-9z" fill="var(--blue)"/><circle cx="6" cy="18" r="2.5" fill="var(--blue)"/><circle cx="18" cy="18" r="2.5" fill="var(--blue)"/></svg></span><h4>Capacity</h4><p>Long-haul driver shortages and limited equipment coupled with growing demand has pushed capacity to a crisis state</p></div>
    <div class="problem" style="top:239px"><span class="strip"></span><span class="icon"><svg width="24" height="24" viewBox="0 0 24 24"><circle cx="6" cy="5" r="3" fill="var(--blue)"/><circle cx="18" cy="5" r="3" fill="var(--blue)"/><path d="M3 22V11h6v11M15 22V11h6v11" fill="var(--blue)"/><rect x="8" y="12" width="8" height="5" fill="var(--blue)"/></svg></span><h4>Services</h4><p>Quality labor has been difficult to source and afford. Virtually all MTI's report a decline in service quality</p></div>
    <div class="problem" style="top:321px"><span class="strip"></span><span class="icon"><svg width="24" height="24" viewBox="0 0 24 24"><circle cx="10" cy="10" r="7" fill="none" stroke="var(--blue)" stroke-width="2.5"/><path d="M15 15l7 7" stroke="var(--blue)" stroke-width="3"/></svg></span><h4>Transparency</h4><p>Too many margin layers...van line, agent, driver and help. In addition, charges are convoluted and confusing</p></div>
    <div class="photo" role="img" aria-label="Mover in blue overalls writing on a clipboard beside a van full of boxes" style="left:402px;top:76px;width:329px;height:319px;background:linear-gradient(135deg,#dedfe2,#c89b65 45%,#2f58c8 85%)"></div>
    <div class="footer"><b>PAGE | <span>04</span></b><span>© 2024 Trovanta | All Rights Reserved</span><span>www.trovanta.com</span></div>
  </section>

  <!-- Solution -->
  <section class="slide" style="left:926px;top:1552px">
    <svg class="header" width="765" height="60"><polygon points="0,0 648,0 625,46 0,46" fill="var(--blue)"/><polygon points="648,0 765,0 765,46 625,46" fill="var(--yellow)"/><polygon points="0,46 408,46 402,58 0,58" fill="var(--yellow)"/></svg>
    <div class="slide-title">The Solution</div>
    <div class="sol-head">TROVANTA'S AI-POWERED PLATFORM</div>
    <div class="sol-list">
      <div class="sol-item"><h4><i></i>CUTTING OUT MIDDLEMEN</h4><p>Trovanta directly connects customers with local movers, eliminating van lines, brokers, and agents. This streamlines the process and ensures transparent, fair pricing.</p></div>
      <div class="sol-item"><h4><i></i>AI-DRIVEN INSTANT PRICING</h4><p>Trovanta offers the industry's only instant, guaranteed pricing using AI, GPS, and key moving variables.</p></div>
      <div class="sol-item"><h4><i></i>AUTOMATED COMPLIANCE</h4><p>Fully automates interstate regulatory compliance, reducing legal risks for all movers in the supply chain.</p></div>
      <div class="sol-item"><h4><i></i>REAL-TIME CAPACITY MATCHING</h4><p>The platform optimizes truck capacity by matching real-time availability with customer move requests, improving operational efficiency.</p></div>
    </div>
    <div class="photo" role="img" aria-label="Two movers unloading stacks of boxes from a van on a city street" style="left:373px;top:82px;width:358px;height:308px;background:linear-gradient(135deg,#cfd3d8,#c2956a 50%,#4a4f5c)"></div>
    <div class="footer"><b>PAGE | <span>08</span></b><span>© 2024 Trovanta | All Rights Reserved</span><span>www.trovanta.com</span></div>
  </section>

</div>
</body>
</html>
```